Birch Hauling Business Card Design Project

We need a new company business card. We provide professional timber harvesting (logging) and forest management services. I'm open to any creative design. Most company caps and shirts are navy blue and Light grey. Logo does not necessarily have to contain those colors. Logo containing picture of logging equipment, log truck, trees, or logs are acceptable. Be creative. Final logo should communicate our company's pride and professionalism in the East Texas Timber Industry.
Updates

Target Market(s)

Timber owners, sawmills, and forestry professionals

Industry/Entity Type

Business

Requirements
Must have
• Must have Contact Info.
Phone: 936-402-5917
address: PO Box 4830
Pine Ridge, Tx 75412
www.jmbirchhauling.example
jmbirchhauling@mailbox.example
Owner: Jared Marsh

Or design must leave room for this info.

```html
<!DOCTYPE html>
<html lang="en">
<head>
<meta charset="utf-8">
<title>Birch Hauling Business Card</title>
<link href="https://fonts.googleapis.com/css2?family=Lato:ital,wght@0,400;0,700;0,900;1,400&display=swap" rel="stylesheet">
<style>
  :root {
    --page-bg: #e9e7e4;
    --front-bg: #231f20;
    --white: #ffffff;
    --navy: #403e92;
    --navy-dark: #2c2a7a;
    --grey: #808080;
    --grey-text: #7a7a7a;
  }
  * { margin: 0; padding: 0; box-sizing: border-box; }
  html, body { width: 1200px; height: 960px; overflow: hidden; }
  body {
    background: var(--page-bg);
    font-family: "Lato", sans-serif;
    position: relative;
  }
  .card {
    position: absolute;
    left: 270px;
    width: 645px;
    height: 368px;
    overflow: hidden;
  }
  .card-front {
    top: 83px;
    background: var(--front-bg);
  }
  .front-name {
    position: absolute;
    left: 0; right: 0; top: 142px;
    text-align: center;
    color: var(--white);
    font-weight: 900;
    font-size: 74px;
    letter-spacing: 1px;
    line-height: 1;
  }
  .front-web {
    position: absolute;
    left: 0; right: 0; top: 311px;
    text-align: center;
    color: var(--white);
    font-style: italic;
    font-size: 19px;
    letter-spacing: 1.5px;
  }
  .card-back {
    top: 507px;
    background: var(--white);
  }
  .brand {
    position: absolute;
    left: 57px; top: 100px;
    display: flex;
    align-items: center;
  }
  .brand-name {
    color: var(--navy);
    font-weight: 900;
    font-size: 22px;
    line-height: 1;
    padding-right: 11px;
  }
  .brand-divider {
    width: 1.5px; height: 36px;
    background: var(--grey);
  }
  .brand-text {
    padding-left: 12px;
    color: var(--grey-text);
    font-size: 14.5px;
    line-height: 18px;
  }
  .brand-text .company { font-weight: 700; }
  .owner {
    position: absolute;
    left: 420px; width: 200px; top: 67px;
    text-align: center;
  }
  .owner-name {
    color: var(--navy-dark);
    font-weight: 700;
    font-size: 20px;
    line-height: 22px;
  }
  .owner-role {
    display: flex; align-items: center; justify-content: center;
    gap: 6px;
    color: var(--grey-text);
    font-size: 13px;
  }
  .owner-role::before, .owner-role::after {
    content: ""; width: 25px; height: 1.5px; background: var(--grey);
  }
  .wave { position: absolute; left: 0; top: 0; }
  .contact {
    position: absolute;
    right: 57px;
    color: var(--white);
    font-size: 14.5px;
    line-height: 19px;
    text-align: right;
  }
  .address { top: 219px; right: 57px; }
  .lines { top: 284px; right: 57px; }
  .contact-row { display: flex; align-items: center; justify-content: flex-end; gap: 8px; }
  .contact-row svg { width: 14px; height: 14px; flex: none; }
</style>
</head>
<body>

<section class="card card-front">
  <div class="front-name">Birch Hauling</div>
  <div class="front-web">www.jmbirchhauling.example</div>
</section>

<section class="card card-back">
  <svg class="wave" width="645" height="368" viewBox="0 0 645 368">
    <path d="M0 196 C60 250 150 262 300 225 C430 190 540 150 645 183 L645 368 L0 368 Z" fill="var(--grey)"/>
    <path d="M0 214 C60 262 150 268 300 232 C430 200 540 162 645 190 L645 368 L0 368 Z" fill="var(--white)"/>
    <path d="M0 218 C60 266 150 272 300 236 C430 204 540 166 645 194 L645 368 L0 368 Z" fill="var(--navy)"/>
  </svg>

  <div class="brand">
    <div class="brand-name">Birch Hauling</div>
    <div class="brand-divider"></div>
    <div class="brand-text">
      <div class="company">Company Name</div>
      <div class="slogan">Your Slogan</div>
    </div>
  </div>

  <div class="owner">
    <div class="owner-name">JARED MARSH</div>
    <div class="owner-role">Owner</div>
  </div>

  <div class="contact address">
    <div>PO Box 4830</div>
    <div>Pine Ridge, Tx 75412</div>
  </div>

  <div class="contact lines">
    <div class="contact-row">936-402-5917
      <svg viewBox="0 0 14 14"><path d="M1 5 C1 2 13 2 13 5 L10 6 L9 4 L5 4 L4 6 Z" fill="#fff"/><rect x="3" y="7" width="8" height="6" rx="1" fill="#fff"/></svg>
    </div>
    <div class="contact-row">jmbirchhauling@mailbox.example
      <svg viewBox="0 0 14 14"><rect x="1" y="3" width="12" height="9" fill="none" stroke="#fff" stroke-width="1.5"/><path d="M1 3 L7 8 L13 3" fill="none" stroke="#fff" stroke-width="1.5"/></svg>
    </div>
    <div class="contact-row">www.jmbirchhauling.example
      <svg viewBox="0 0 14 14"><rect x="1" y="2" width="12" height="8" fill="none" stroke="#fff" stroke-width="1.5"/><rect x="4" y="12" width="6" height="1.5" fill="#fff"/></svg>
    </div>
  </div>
</section>

</body>
</html>
```